Wordpress Design for a Digital Management Consulting Business

I need a simple Wordpress Design and someone to set it up for a new boutique management consulting business called Quillon Advisory that specialises in providing strategic advice to help grow digital businesses. It covers business strategy, marketing strategy, digital strategy, web product development, marketing campaigns, social, search, etc. From strategy to implementation.

URL is: quillonadvisory.com.au

My professional background is here: au.linkedin.com/in/hollyprenwick

Competitors: other boutique digital/marketing management consulting businesses in Australia

The logos, colours and fonts are attached.

I would like the site to convey a business that is Smart/intelligent, Contemporary, Progressive, Digital, Energetic, Friendly.

The objective of the site is to educate visitors about what Quillon Advisory does and encourage them to contact me for more information. It will be very light on content.

Target Market(s)

CEOs/Managing Directors, General Managers, Marketing Directors

Industry/Entity Type

Management Consulting

Font styles to use
Sans Serif

Colors
e34197
5c5c5c
000000

Requirements
Must have
• Site design requirements:
• Choose an appropriate Wordpress template, set it up for me and let me be able to edit it ongoing.
• It should use lots of images - these can be inspirational and not necessarily tied directly to the work
• Pink should feature, but not be the dominant colour.
• Site structure should be:
• 1. Home page - image led with horizontal navigation. Text beneath and images to describe the services.
• 2. About page - with space to write text and insert a picture of the Director
• 3. Services - with space to highlight services either as a list or graphically with text
• 4. Contact page - with space to write text and add email links, etc.
• Should have horizontal navigation
• It should have the flexibility to add another page
Nice to have
• Use the tree icon somehow in the design - consider in the background enlarged
• Use pink, grey, black from logo. Can introduce another complimentary colour if necessary.
• Can introduce another complimentary font to go with the logo font.
Should not have
• Use cliched business images and icons, eg. business suits, hand shakes, business men, business ties.

```html
<!DOCTYPE html>
<html lang="en">
<head>
<meta charset="utf-8">
<title>Quillon Advisory</title>
<link href="https://fonts.googleapis.com/css2?family=Open+Sans:wght@400;600;700&family=Raleway:wght@300;400&display=swap" rel="stylesheet">
<style>
  :root {
    --pink: #e34197;
    --pink-dark: #c92f80;
    --grey: #5c5c5c;
    --grey-dark: #4a4a4a;
    --black: #000000;
    --light: #ececec;
    --white: #ffffff;
    --text: #666666;
  }
  * { box-sizing: border-box; margin: 0; padding: 0; }
  html, body { width: 805px; height: 1200px; overflow: hidden; background: var(--white); }
  body { font-family: "Open Sans", Arial, sans-serif; color: var(--text); position: relative; }
  a { text-decoration: none; }

  .site-header { height: 80px; display: flex; justify-content: space-between; align-items: center; padding: 0 67px; }
  .brand { display: flex; align-items: center; gap: 10px; }
  .brand-mark { width: 26px; height: 26px; border-radius: 50%; background: var(--pink); }
  .brand-name { font-family: "Open Sans", Arial, sans-serif; font-weight: 400; font-size: 24px; color: var(--pink); white-space: nowrap; }
  .contact-list { list-style: none; font-size: 11px; color: var(--pink); }
  .contact-list li { display: flex; align-items: center; gap: 8px; margin: 6px 0; }
  .contact-list .muted { color: var(--grey); }
  .contact-list svg { width: 14px; height: 14px; }

  .main-nav { height: 38px; background: var(--pink); padding: 0 67px; display: flex; }
  .main-nav a { color: var(--white); font-size: 10px; font-weight: 600; text-transform: uppercase; padding: 0 17px; line-height: 38px; }
  .main-nav a.active { background: var(--black); }

  .hero { position: relative; height: 324px; background: linear-gradient(180deg, #f1f1f1, #dcdcdc); overflow: hidden; }
  .hero-map { position: absolute; left: 120px; top: 20px; width: 640px; height: 230px; border-radius: 40% 50% 45% 40%; background: radial-gradient(ellipse at center, #c9c9c9 0%, rgba(210,210,210,0.5) 55%, rgba(230,230,230,0) 75%); }
  .hero-portrait { position: absolute; left: 95px; top: 0; width: 250px; height: 324px; background: linear-gradient(180deg, #3b3338 0%, #2a2428 50%, #5a7faa 100%); border-radius: 120px 120px 0 0; }
  .hero-copy { position: absolute; left: 392px; top: 158px; width: 330px; }
  .hero-copy h1 { font-family: "Raleway", sans-serif; font-weight: 400; font-size: 30px; color: var(--grey-dark); margin-bottom: 14px; }
  .hero-copy p { font-size: 12px; line-height: 1.55; color: var(--grey); margin-bottom: 16px; }
  .read-more { display: inline-flex; height: 30px; }
  .read-more .label { background: var(--pink); color: var(--white); font-size: 12px; font-weight: 600; padding: 0 12px; line-height: 30px; }
  .read-more .arrow { background: var(--grey); width: 30px; display: flex; align-items: center; justify-content: center; }

  .section-title { text-align: center; font-family: "Raleway", sans-serif; font-weight: 300; font-size: 34px; letter-spacing: 5px; text-transform: uppercase; }
  .divider { display: flex; justify-content: center; align-items: center; gap: 6px; margin-top: 8px; }
  .divider .line { width: 50px; height: 1px; background: currentColor; opacity: .6; }
  .divider .dot { width: 4px; height: 4px; border-radius: 50%; background: currentColor; }

  .services { padding-top: 50px; height: 363px; color: var(--black); }
  .card-row { display: flex; justify-content: space-between; padding: 0 67px; margin-top: 38px; }
  .card { width: 200px; background: var(--white); box-shadow: 0 1px 4px rgba(0,0,0,.15); padding-bottom: 14px; }
  .card-image { height: 100px; }
  .card h3 { color: var(--pink); font-weight: 400; font-size: 15px; margin: 10px 8px 6px; line-height: 1.15; }
  .card p { font-size: 10px; line-height: 1.5; margin: 0 8px; color: var(--text); }
  .img-blue { background: linear-gradient(135deg, #8bb9e0, #3d7fc1); }
  .img-office { background: linear-gradient(135deg, #e5e5e5, #7a7a7a); }
  .img-tech { background: linear-gradient(135deg, #274a86, #9fc3ea); }
  .img-team { background: linear-gradient(135deg, #e8dcd0, #9c6f58); }
  .img-desk { background: linear-gradient(135deg, #f0f0f0, #a7b4c4); }
  .img-talk { background: linear-gradient(135deg, #f3e9e4, #5c4b48); }

  .what-we-do { height: 357px; background: linear-gradient(180deg, #5e5e5e, #4f4f4f); padding-top: 40px; color: var(--white); }
  .what-we-do .card-row { margin-top: 30px; }
  .what-we-do .card { min-height: 218px; }

  .site-footer { position: absolute; bottom: 0; left: 0; width: 805px; height: 38px; background: var(--pink); color: var(--white); font-size: 10px; text-align: center; line-height: 38px; }
</style>
</head>
<body>
  <header class="site-header">
    <div class="brand">
      <div class="brand-mark"></div>
      <div class="brand-name">Quillon Advisory</div>
    </div>
    <ul class="contact-list">
      <li>
        <svg viewBox="0 0 24 24" fill="var(--grey)"><path d="M6.6 10.8a15 15 0 0 0 6.6 6.6l2.2-2.2c.3-.3.7-.4 1-.2 1.1.4 2.3.6 3.6.6.6 0 1 .4 1 1V20c0 .6-.4 1-1 1A17 17 0 0 1 3 4c0-.6.4-1 1-1h3.5c.6 0 1 .4 1 1 0 1.3.2 2.5.6 3.6.1.3 0 .7-.2 1z"/></svg>
        <span>Holly Prenwick</span><span class="muted">0400 118 352</span>
      </li>
      <li>
        <svg viewBox="0 0 24 24" fill="none" stroke="var(--grey)" stroke-width="2"><rect x="3" y="5" width="18" height="14"/><path d="M3 6l9 7 9-7"/></svg>
        <span>holly@quillonadvisory.com.au</span>
      </li>
    </ul>
  </header>

  <nav class="main-nav">
    <a class="active" href="#">Home</a>
    <a href="#">Services</a>
    <a href="#">What we do</a>
    <a href="#">About</a>
    <a href="#">Director Holly Prenwick</a>
    <a href="#">Clients</a>
    <a href="#">Contact</a>
  </nav>

  <section class="hero">
    <div class="hero-map" role="img" aria-label="Faint world map backdrop"></div>
    <div class="hero-portrait" role="img" aria-label="Photo of a smiling consultant holding a tablet"></div>
    <div class="hero-copy">
      <h1>Quillon Advisory</h1>
      <p>Is a boutique management consulting company advising digital businesses across business, product and marketing strategy.</p>
      <a class="read-more" href="#"><span class="label">Read More</span><span class="arrow"><svg width="12" height="12" viewBox="0 0 12 12"><path d="M2 6h8M7 3l3 3-3 3" stroke="#fff" stroke-width="1.6" fill="none"/></svg></span></a>
    </div>
  </section>

  <section class="services">
    <h2 class="section-title">Services</h2>
    <div class="divider"><span class="line"></span><span class="dot"></span><span class="dot"></span><span class="line"></span></div>
    <div class="card-row">
      <article class="card">
        <div class="card-image img-blue" role="img" aria-label="Photo of hands working with a tablet and charts"></div>
        <h3>Digital Strategy</h3>
        <p>Lorem Ipsum has been the industry's standard dummy text ever since the 1500s, when an unknown printer</p>
      </article>
      <article class="card">
        <div class="card-image img-office" role="img" aria-label="Photo of a person presenting at a whiteboard"></div>
        <h3>Marketing strategy</h3>
        <p>Lorem Ipsum has been the industry's standard dummy text ever since the 1500s, when an unknown printer</p>
      </article>
      <article class="card">
        <div class="card-image img-tech" role="img" aria-label="Photo of a digital interface concept"></div>
        <h3>Digital Transformation</h3>
        <p>Lorem Ipsum has been the industry's standard dummy text ever since the 1500s, when an unknown printer</p>
      </article>
    </div>
  </section>

  <section class="what-we-do">
    <h2 class="section-title">What we do</h2>
    <div class="divider"><span class="line"></span><span class="dot"></span><span class="dot"></span><span class="line"></span></div>
    <div class="card-row">
      <article class="card">
        <div class="card-image img-team" role="img" aria-label="Photo of a team in discussion"></div>
        <h3>Strategic Thinking</h3>
        <p>Lorem Ipsum has been the industry's standard dummy text ever since the 1500s, when an unknown printer</p>
      </article>
      <article class="card">
        <div class="card-image img-desk" role="img" aria-label="Photo of a desk with reports and a laptop"></div>
        <h3>Analytical Approach</h3>
        <p>Lorem Ipsum has been the industry's standard dummy text ever since the 1500s, when an unknown printer</p>
      </article>
      <article class="card">
        <div class="card-image img-talk" role="img" aria-label="Photo of colleagues meeting"></div>
        <h3>End to end project Management</h3>
        <p>Lorem Ipsum has been the industry's standard dummy text ever since the 1500s, when an unknown printer</p>
      </article>
    </div>
  </section>

  <footer class="site-footer">© 2015 Copyright Quillon Advisory, All Rights Reserved</footer>
</body>
</html>
```